Wordpress Design Project

We are an online jewellery business currently trading entirely online through internet auctions.

We are revamping our online operations. We want to launch our website. Which will incorporate extensive social media integration. Chatterloop, Blogging to chatterloop as well as Boardquill. These need to be linked (some and/or interactive).

We want to collect subscriptions and collate emails/info.

There may also be video uploads of our stock.

Whilst we are Sydney based we see ourselves as a global business.

We sell High End exclusive designer jewellery.
Often bespoke pieces of diamond jewellery.

Words that some up our brand personality
Savvy, Stylish, Confident, Approachable

About our style
Ensuring not only that our designs and jewellery have a certain sense of classic or fashion-driven style, but expressing style and beauty through all touch points. We understand that style is not only about what you wear, but how you carry yourself.

About our company mission
Make precious jewellery an affordable luxury for stylish, savvy buyers
Create products that we're proud to sell and that customers desire, treasure and proudly wear.

KEY FOCUS/OUTCOME:

We require a stylish, clean, visually easy to navigate website. Main aim of the site is to showcase products. Not a shop per se. Ultimate goal is to engage the viewer to ask us to make something special for them. Not a huge budget. WE are a small business. But we make beautiful fine jewellery. Focus on Blog, social media interactions important, Innovative WORDPRESS design. Think special. We want to be inspired as we are inspired by some of the links we've presented here. They give a great overall feel of what we are looking for.

We require full implementation to be delivered.

http://www.tarvoselk.com/
http://www.merovatrikes.com/
http://www.fenwardspirit.com/cocktails/
www.plomarn.ch
http://www.vuralette.fr/en

SEO expertise as well as adaptation across all mobile devices/tablets.

Requirements
Must have
• Social Media, Blog, unique design (not same-same) Has to feel bespoke. 48 hour "buy it now" feature. Like a daily deal function with the ability to check out through CoinVeil. One high ticket item per day. Easy for us to manipulate/upload to website. User friendly.
Fast website. Not slow.
Should not have
• -should not look like a traditional shopping cart.

```html
<!DOCTYPE html>
<html lang="en">
<head>
<meta charset="utf-8">
<title>Verandi — designer jewellery</title>
<link href="https://fonts.googleapis.com/css2?family=Source+Sans+3:wght@400;600&display=swap" rel="stylesheet">
<style>
  :root {
    --ink: #111111;
    --white: #ffffff;
    --text: #2b2b2b;
    --nav-top: #3a3a3a;
    --nav-bottom: #0c0c0c;
    --footer: #efefef;
    --bottom-bar: #8a8a8a;
    --field: #cfcfcf;
    --social-blue: #3b5b9e;
    --social-sky: #2d9ad6;
    --social-red: #c41e2a;
    --social-crimson: #e02a22;
  }
  * { box-sizing: border-box; margin: 0; padding: 0; }
  html, body { width: 930px; height: 1200px; overflow: hidden; }
  body {
    position: relative;
    background: var(--white);
    font-family: "Source Sans 3", "Helvetica Neue", Arial, sans-serif;
    color: var(--text);
  }
  .top-strip { position: absolute; left: 0; top: 0; width: 930px; height: 6px; background: var(--ink); }

  .brand {
    position: absolute; left: 70px; top: 42px;
    display: flex; align-items: center; gap: 10px;
    color: var(--ink); font-size: 30px; font-weight: 600; letter-spacing: 2px; line-height: 1;
  }
  .brand-square { width: 14px; height: 14px; background: var(--ink); }

  .account-links {
    position: absolute; left: 492px; top: 25px; display: flex; gap: 12px;
    font-size: 11.5px; font-weight: 600; color: var(--ink); letter-spacing: .2px;
  }
  .account-links .sep { font-weight: 400; }
  .cart { position: absolute; left: 768px; top: 23px; font-size: 12.5px; color: var(--ink); display: flex; align-items: center; gap: 6px; }

  .search {
    position: absolute; left: 687px; top: 60px; width: 176px; height: 27px;
    border: 1px solid #c8c8c8; border-radius: 2px; background: var(--white);
    font-size: 10.5px; font-style: italic; color: #999; padding: 6px 5px;
  }
  .search svg { position: absolute; right: 8px; top: 7px; }

  .main-nav {
    position: absolute; left: 0; top: 126px; width: 930px; height: 49px;
    background: linear-gradient(var(--nav-top), var(--nav-bottom));
    display: flex; align-items: center; padding-left: 68px;
  }
  .main-nav a {
    color: var(--white); text-decoration: none; font-size: 12.5px; font-weight: 600;
    letter-spacing: .2px; margin-right: 35px;
  }
  .main-nav a:last-child { margin-right: 0; }

  .hero {
    position: absolute; left: 0; top: 175px; width: 930px; height: 478px;
    background:
      radial-gradient(ellipse 300px 220px at 430px 230px, #c9a894 0%, #8c6c58 45%, transparent 75%),
      radial-gradient(ellipse 260px 200px at 760px 360px, #a48358 0%, transparent 70%),
      linear-gradient(100deg, #6f6150 0%, #3c2f25 40%, #1a1410 75%, #0c0907 100%);
  }
  .slide-dots { position: absolute; left: 72px; top: 631px; display: flex; gap: 2px; }
  .slide-dots span { width: 9px; height: 9px; border-radius: 50%; border: 1px solid #ddd; background: rgba(255,255,255,.25); }
  .slide-dots span.active { background: #f0f0f0; }

  .collection-menu {
    position: absolute; left: 67px; top: 175px; width: 105px;
    background: rgba(10,10,10,.88); list-style: none;
  }
  .collection-menu li {
    height: 22.5px; line-height: 22.5px; padding-left: 14px;
    color: var(--white); font-size: 10.5px; letter-spacing: .3px;
    border-bottom: 1px solid #2a2a2a;
  }

  .products-title { position: absolute; left: 70px; top: 678px; font-size: 17px; font-weight: 600; color: #333; }
  .carousel-arrows { position: absolute; left: 823px; top: 679px; display: flex; gap: 3px; }
  .carousel-arrows span { width: 18px; height: 18px; border-radius: 50%; background: #8c8c8c; display: flex; align-items: center; justify-content: center; }

  .product-card { position: absolute; top: 720px; height: 229px; background: #050505; overflow: hidden; }
  .product-photo { position: absolute; inset: 0; }
  .product-card .caption {
    position: absolute; left: 0; right: 0; bottom: 0; height: 41px;
    background: rgba(0,0,0,.55); color: var(--white);
    font-size: 14.5px; line-height: 41px; padding-left: 11px; white-space: nowrap;
  }

  .site-footer { position: absolute; left: 0; top: 989px; width: 930px; height: 165px; background: var(--footer); }
  .footer-heading { position: absolute; top: 17px; font-size: 13px; font-weight: 600; color: #333; letter-spacing: .2px; }
  .care-list { position: absolute; left: 73px; top: 48px; list-style: none; font-size: 12.5px; color: #333; }
  .care-list li { height: 24px; }
  .newsletter-field { position: absolute; left: 695px; top: 46px; width: 158px; height: 26px; background: var(--field); border: 1px solid #c4c4c4; }
  .newsletter-field svg { position: absolute; right: 5px; top: 7px; }
  .social-row { position: absolute; left: 695px; top: 118px; display: flex; gap: 10px; }
  .social-row .badge { width: 28px; height: 28px; }

  .bottom-bar { position: absolute; left: 0; top: 1154px; width: 930px; height: 46px; background: var(--bottom-bar); color: var(--white); }
  .copyright { position: absolute; left: 73px; top: 15px; font-size: 11px; }
  .pay-row { position: absolute; left: 691px; top: 13px; display: flex; gap: 2px; }
  .pay-row span {
    height: 20px; padding: 0 4px; background: var(--white); color: #333;
    font-size: 9px; line-height: 20px; border-radius: 2px;
  }
</style>
</head>
<body>
  <div class="top-strip"></div>

  <header>
    <div class="brand"><span class="brand-square"></span><span>VERANDI</span></div>

    <nav class="account-links">
      <span>MY ACCOUNT</span><span class="sep">|</span>
      <span>SIGN IN</span><span class="sep">|</span>
      <span>CHECK OUT</span>
    </nav>

    <div class="cart">
      <svg width="16" height="14" viewBox="0 0 16 14" aria-hidden="true">
        <path d="M1 1h3l2 8h8l1.5-6H5" fill="none" stroke="#555" stroke-width="1.3"/>
        <circle cx="7" cy="12" r="1.3" fill="#555"/><circle cx="13" cy="12" r="1.3" fill="#555"/>
      </svg>
      <span>Cart (0) items</span>
    </div>

    <div class="search">Search..
      <svg width="11" height="11" viewBox="0 0 11 11" aria-hidden="true">
        <circle cx="4.5" cy="4.5" r="3.5" fill="none" stroke="#888" stroke-width="1.5"/>
        <path d="M7 7l3 3" stroke="#888" stroke-width="1.6"/>
      </svg>
    </div>
  </header>

  <section class="hero" role="img" aria-label="Portrait of a woman with long curly hair wearing gold spiral earrings and a matching gold pendant"></section>

  <nav class="main-nav">
    <a>COLLECTION GALLERY</a>
    <a>ABOUT US</a>
    <a>BLOG</a>
    <a>EDUCATION</a>
    <a>BUYING FROM US</a>
    <a>TESTIMONIALS</a>
    <a>48 HOUR PRODUCT OFFER</a>
  </nav>

  <ul class="collection-menu">
    <li>RINGS</li><li>WATCHES</li><li>BRACELETS</li><li>EARRINGS</li>
  </ul>

  <div class="slide-dots"><span class="active"></span><span></span><span></span><span></span></div>

  <h2 class="products-title">PRODUCTS</h2>
  <div class="carousel-arrows">
    <span><svg width="8" height="8" viewBox="0 0 8 8" aria-hidden="true"><path d="M5.5 1L2.5 4l3 3" fill="none" stroke="#fff" stroke-width="1.6"/></svg></span>
    <span><svg width="8" height="8" viewBox="0 0 8 8" aria-hidden="true"><path d="M2.5 1l3 3-3 3" fill="none" stroke="#fff" stroke-width="1.6"/></svg></span>
  </div>

  <article class="product-card" style="left:70px;width:244px">
    <div class="product-photo" role="img" aria-label="Diamond-set spiral pendant on a silver chain" style="background:radial-gradient(circle 70px at 122px 150px,#8a8a8a,#2a2a2a 60%,#050505)"></div>
    <div class="caption">Sit amet conse ctetur adipisicing elit</div>
  </article>
  <article class="product-card" style="left:345px;width:242px">
    <div class="product-photo" role="img" aria-label="Gold bracelet set with square diamonds" style="background:radial-gradient(ellipse 110px 60px at 121px 140px,#8e7a52,#2e2617 60%,#050505)"></div>
    <div class="caption">Sit amet conse ctetur adipisicing elit</div>
  </article>
  <article class="product-card" style="left:618px;width:242px">
    <div class="product-photo" role="img" aria-label="Emerald-cut amethyst ring with diamond side stones" style="background:radial-gradient(ellipse 60px 80px at 121px 90px,#8f64b0,#2f1f3c 60%,#050505)"></div>
    <div class="caption">Sit amet conse ctetur adipisicing elit</div>
  </article>

  <footer class="site-footer">
    <h3 class="footer-heading" style="left:73px">CUSTOMER CARE</h3>
    <h3 class="footer-heading" style="left:220px">FAQ</h3>
    <h3 class="footer-heading" style="left:293px">CONTACT US</h3>
    <h3 class="footer-heading" style="left:415px">TERMS &amp; CONDITIONS</h3>
    <h3 class="footer-heading" style="left:592px">SITE MAP</h3>
    <h3 class="footer-heading" style="left:695px">NEWS LETTER</h3>

    <ul class="care-list">
      <li>Product Information</li>
      <li>Shipping &amp; Delivery</li>
      <li>Returns &amp; Exchanges</li>
      <li>Privacy &amp; Security</li>
    </ul>

    <div class="newsletter-field">
      <svg width="13" height="11" viewBox="0 0 13 11" aria-hidden="true">
        <path d="M1 1l4 4.5-4 4.5M7 1l4 4.5-4 4.5" fill="none" stroke="#fff" stroke-width="1.4"/>
      </svg>
    </div>

    <h3 class="footer-heading" style="left:695px;top:90px">GET CONNECTED TO US</h3>
    <div class="social-row">
      <span class="badge" style="background:var(--social-blue)" aria-label="Chatterloop"></span>
      <span class="badge" style="background:var(--social-sky)" aria-label="Chirpwave"></span>
      <span class="badge" style="background:var(--social-red)" aria-label="Boardquill"></span>
      <span class="badge" style="background:var(--social-crimson)" aria-label="Reelcast"></span>
    </div>
  </footer>

  <div class="bottom-bar">
    <p class="copyright">© 2013 Copyrights Reserved. All rights reserved.</p>
    <div class="pay-row"><span>Paxa</span><span>Corvex</span><span>CoinVeil</span><span>Dualpay</span></div>
  </div>
</body>
</html>
```